Revamp Website To A More Modern Up To Date Design Concepts

I am looking for a renewed look for my website.

Keep in mind that my business is B2B.

Please use and include all current content, text and imagery (you can adjust the imagery to fit your designs) and all current modules, features, videos, calls to action buttons, etc. Please do not omit anything from the current homepage. I prefer to see all my content as it is on my current site on the new design too so I can really invision my new site...so please do not use lipsum lorem text filler anywhere.

I am looking for an impressive looking and engaging high converting homepage.

Please be sure to keep all elements, links in header and footer etc. already on my current homepage at www.brightlanepromoworks.biz

Industry/Entity Type

marketing

Coding

Coded - Design and coding required

Number of Pages Required

3 page

Requirements
Must have
• impressive design
Nice to have
• im open
Should not have
• open

```html
<!DOCTYPE html>
<html lang="en">
<head>
<meta charset="utf-8">
<title>BrightLane Promo Works – Homepage Concepts</title>
<link href="https://fonts.googleapis.com/css2?family=Poppins:wght@300;400;500;600;700&display=swap" rel="stylesheet">
<style>
:root{
  --bg:#dde6f0;
  --blue:#1a73c9;
  --blue-lt:#3d8fe0;
  --dark:#1c1c21;
  --ink:#222228;
  --muted:#6d6f78;
  --line:#d9dbe2;
  --grey:#eeeff2;
  --navy:#2b1f86;
  --green:#2fb36b;
  --white:#fff;
}
*{box-sizing:border-box;margin:0;padding:0}
html,body{width:1200px;height:1150px;overflow:hidden;background:var(--bg)}
body{font-family:"Poppins",sans-serif;color:var(--ink)}
.stage{position:absolute;left:0;top:0;width:1960px;height:1878px;transform:scale(.6122);transform-origin:0 0}
.page{position:absolute;width:606px;background:var(--white);overflow:hidden;box-shadow:0 6px 24px rgba(40,60,100,.12)}
.a{position:absolute}
.btn{position:absolute;height:20px;padding:0 14px;border-radius:10px;background:var(--blue);color:#fff;font-size:6.4px;font-weight:600;line-height:20px;white-space:nowrap}
.btn.c{transform:translateX(-50%)}
.h-sec{font-weight:600;letter-spacing:.3px;text-transform:uppercase}
.txt{font-size:6.4px;line-height:1.6;color:var(--muted)}
.on-dark{color:#c8c9d2}
.ph{position:absolute}
.play{position:absolute;width:30px;height:30px;border-radius:50%;background:#fff;transform:translate(-50%,-50%)}
.play::after{content:"";position:absolute;left:12px;top:9px;border-left:10px solid var(--blue);border-top:6px solid transparent;border-bottom:6px solid transparent}
.brand{font-weight:600;color:var(--blue);font-size:9px;letter-spacing:.4px;white-space:nowrap;display:flex;align-items:center;gap:5px}
.brand i{width:12px;height:12px;background:var(--blue);display:inline-block}
.chk li{list-style:none;position:relative;padding-left:11px;font-size:6.4px;line-height:1.55;margin-bottom:6px}
.chk li::before{content:"";position:absolute;left:0;top:1.5px;width:7px;height:7px;border-radius:50%;background:var(--green)}
.chk li::after{content:"";position:absolute;left:2.3px;top:2.8px;width:2px;height:3.5px;border:solid #fff;border-width:0 1px 1px 0;transform:rotate(45deg)}
.topbar{position:absolute;left:0;top:0;width:606px;height:25px;background:var(--blue);color:#fff;font-size:6.2px;font-weight:500}
.topbar span{position:absolute;top:8px}
.nav a{position:absolute;top:45px;font-size:6.8px;color:#555;text-decoration:none}
.stats .n{color:var(--blue-lt);font-size:8.5px;font-weight:500}
.stats div{position:absolute;width:70px;text-align:center;font-size:6.2px;line-height:1.45;color:#b9bac4}
.thumb{position:absolute;top:375px;width:64px;height:83px;border:2px solid #fff}
.acc{position:absolute;left:267px;width:285px;height:40px;border-bottom:1px solid var(--line);font-size:6.6px;font-weight:600;line-height:40px;padding-left:28px}
.acc::before{content:"";position:absolute;left:2px;top:12px;width:14px;height:15px;border:1.2px solid var(--blue);border-radius:2px}
.acc::after{content:"";position:absolute;right:3px;top:17px;width:4px;height:4px;border:solid var(--blue);border-width:0 1px 1px 0;transform:rotate(45deg)}
.acc.open{color:var(--blue);border-bottom:none}
.acc.open::after{transform:rotate(-135deg);top:19px}
.ring-ic{position:absolute;width:36px;height:36px;border-radius:50%;border:1.3px solid var(--blue);background:#fff;transform:translate(-50%,-50%)}
.ring-ic::after{content:"";position:absolute;left:11px;top:11px;width:12px;height:12px;border:1.2px solid var(--blue);border-radius:3px}
.logo-box{position:absolute;width:160px;height:71px;background:#fff;display:flex;align-items:center;justify-content:center;font-size:12px;font-weight:500;color:#2a2a2e;letter-spacing:.5px}
.bul{position:absolute;left:55px;width:320px}
.bul p{position:relative;padding-left:9px;font-size:6.3px;line-height:1.6;color:var(--muted);margin-bottom:9px}
.bul p::before{content:"";position:absolute;left:0;top:4px;width:3px;height:3px;border-radius:50%;background:var(--blue)}
.step{position:absolute;left:216px;display:flex;align-items:center;gap:10px;font-size:6.2px;color:var(--muted)}
.step i{width:30px;height:30px;border-radius:50%;border:1.2px solid var(--blue);background:#fff;flex:none;position:relative}
.step i::after{content:"";position:absolute;left:10px;top:10px;width:8px;height:8px;border:1.2px solid var(--blue);border-radius:2px}
.step b{color:var(--ink)}
.fcol h4{font-size:6.4px;font-weight:600;padding-bottom:8px;border-bottom:1px solid var(--line);margin-bottom:10px}
.fcol p{font-size:6.3px;color:var(--muted);line-height:1.55;margin-bottom:9px}
.fcol .t{color:var(--ink);font-weight:600}
.soc{position:absolute;top:773px;width:10px;height:10px;border-radius:50%;background:var(--blue)}
</style>
</head>
<body>
<div class="stage">

<section class="page" style="left:35px;top:35px;height:1807px">
  <div class="topbar">
    <span style="left:66px">Call or Text ⌄</span>
    <span style="left:137px">Book a Demo ⌄</span>
    <span style="left:442px">⟶ LOGIN</span>
    <span style="left:500px">◯ SIGN UP</span>
  </div>
  <div class="a brand" style="left:55px;top:43px"><i></i>BRIGHTLANE PROMO WORKS</div>
  <nav class="nav">
    <a style="left:257px;color:var(--blue);border-bottom:1px solid var(--blue)">Home</a>
    <a style="left:297px">Incentives List</a>
    <a style="left:365px">Get Free Samples</a>
    <a style="left:446px">Integrations</a>
    <a style="left:507px">Industries ⌄</a>
  </nav>

  <h1 class="a h-sec" style="left:55px;top:125px;width:250px;font-size:20.5px;line-height:1.3">2X-5X Your Sales &amp; Leads Overnight</h1>
  <p class="a" style="left:55px;top:200px;width:205px;font-size:10.5px;line-height:1.55;color:var(--muted);font-weight:300">Give a complementary high value incentives as a bonus gift with the purchase of your product or service.</p>
  <div class="btn" style="left:55px;top:268px">Sign Up For a 14 Day Risk Free Trial</div>
  <div class="ph" role="img" aria-label="Fanned stack of colourful travel and dining gift certificates circled by green and blue arrows" style="left:330px;top:112px;width:220px;height:190px;border-radius:28px;background:linear-gradient(135deg,#3fb7c7 0%,#f2a33a 45%,#e4496d 75%,#6a3fa3 100%);opacity:.85"></div>

  <div class="a" style="left:0;top:340px;width:606px;height:331px;background:var(--dark)"></div>
  <div class="thumb" role="img" aria-label="Dining certificate flyer" style="left:55px;background:linear-gradient(#c9723a,#f0d0a6)"></div>
  <div class="thumb" role="img" aria-label="Wine certificate flyer" style="left:142px;background:linear-gradient(#e4b23a,#f6ecd0)"></div>
  <div class="thumb" role="img" aria-label="Restaurant certificate flyer" style="left:228px;background:linear-gradient(#b34646,#f2c8c8)"></div>
  <div class="thumb" role="img" aria-label="Airfare certificate flyer" style="left:315px;background:linear-gradient(#d36c3a,#f5d2b6)"></div>
  <div class="thumb" role="img" aria-label="Cruise certificate flyer" style="left:401px;background:linear-gradient(#3d7fc6,#cfe2f5)"></div>
  <div class="thumb" style="left:488px;background:#222;border-color:#333;color:#fff;text-align:center;font-size:6.6px;padding-top:14px;line-height:1.4">Resort<br>Certificates<span style="display:block;margin-top:9px;font-size:5.6px;color:#bbb">Complimentary<br>All Inclusive<br>Vacations</span></div>

  <div class="stats">
    <div style="left:58px;top:517px"><span class="n">16+</span><br>Years<br>In Business</div>
    <div style="left:135px;top:517px"><span class="n">17K+</span><br>Clients<br>Enrolled</div>
    <div style="left:212px;top:517px"><span class="n">11M+</span><br>Certificates<br>Circulated</div>
    <div style="left:58px;top:581px"><span class="n">400K</span><br>Incentives<br>Redeemed</div>
    <div style="left:135px;top:581px"><span class="n">$20M+</span><br>In Savings<br>For Redeemers</div>
    <div style="left:212px;top:581px"><span class="n">100's</span><br>Reviews &amp;<br>Testimonials</div>
  </div>
  <h2 class="a h-sec" style="left:321px;top:495px;width:235px;font-size:13.4px;line-height:1.33;color:#fff">Give Away An Unlimited Amount Of Complimentary Redeemable Gift Vouchers</h2>
  <p class="a" style="left:321px;top:570px;width:235px;font-size:8.3px;line-height:1.55;color:#d0d1d8">Without having to personally fulfill or pay for any of them yourself!</p>
  <div class="btn" style="left:321px;top:615px">Sign Up For a 14 Day Risk Free Trial</div>

  <h2 class="a h-sec" style="left:55px;top:772px;width:200px;font-size:13.4px;line-height:1.33">The 4 Major Areas That Matter Most To Your Business</h2>
  <div class="a" style="left:55px;top:838px;width:30px;height:1px;background:var(--blue)"></div>
  <p class="a" style="left:55px;top:848px;width:170px;font-size:8px;line-height:1.55;color:var(--muted)">And how using high value incentives seamlessly integrates with them.</p>
  <div class="btn" style="left:55px;top:896px">Sign Up For a 14 Day Risk Free Trial</div>
  <div class="a" style="left:296px;top:725px;width:238px;height:238px;border:1px dashed var(--line);border-radius:50%"></div>
  <div class="ring-ic" style="left:415px;top:725px;background:var(--blue);width:40px;height:40px"></div>
  <div class="ring-ic" style="left:296px;top:843px"></div>
  <div class="ring-ic" style="left:534px;top:843px"></div>
  <div class="ring-ic" style="left:415px;top:962px"></div>
  <div class="a" style="left:330px;top:767px;width:170px;text-align:center">
    <div style="color:var(--blue);font-size:8.2px;font-weight:500">More Leads</div>
    <p class="txt" style="margin-top:5px">Want to see an explosion in response rates of your existing marketing efforts?</p>
    <div style="font-size:6.3px;font-weight:600;margin:4px 0">Use Case</div>
    <p class="txt">Use one (or more) of the incentives that come with your BrightLane package as a simple tagline. For example: "Submit your details today and you will receive a FREE Smartwatch or $100 Dining Card, No Purchase Necessary... just for learning about our company"</p>
    <div style="display:inline-block;margin-top:6px;border:1px solid var(--line);border-radius:10px;padding:2px 13px;font-size:6.3px;color:var(--blue)">Read More</div>
  </div>

  <div class="ph" role="img" aria-label="Man working on a laptop under a purple overlay" style="left:55px;top:1015px;width:195px;height:462px;background:linear-gradient(180deg,#3b2aa0 0%,#4a3aa8 45%,#2c2570 100%)"></div>
  <h2 class="a h-sec" style="left:73px;top:1034px;width:170px;font-size:13.4px;line-height:1.33;color:#fff">Distribute Valued Package Incentives</h2>
  <p class="a" style="left:73px;top:1090px;font-size:8px;color:#d8d4f4">Branded with your logo</p>
  <div class="btn" style="left:73px;top:1440px">Sign Up For a 14 Day Risk Free Trial</div>

  <div class="acc" style="top:1015px">Tangible Printable PDF Certificates</div>
  <div class="acc" style="top:1055px">Send Digital E-Certificates By Email</div>
  <div class="acc" style="top:1094px">QR Codes, Web Banners, Linkflow and API Integrations</div>
  <div class="acc" style="top:1134px">SMS Certificates</div>
  <div class="acc open" style="top:1173px">Eye-Catching Pop-Ups and Sticky Bars</div>
  <p class="a txt" style="left:267px;top:1213px;width:285px">Want an influx of high-converting leads? Simply install our attractive and customizable pop-ups and sticky bars on your site and watch your conversions explode! Dana Whitfield reported seeing a 46% increase in sign-ups after implementing pop-ups on his personal blog, whitfieldgrowth.com (without using high value incentives!). PostCraft credits its sticky bar with a 25% increase in subscriptions. (Imagine adding high value incentives to boot!)</p>
  <div class="a" style="left:267px;top:1287px;width:285px;height:1px;background:var(--blue)"></div>
  <div class="ph" role="img" aria-label="Video still of a presenter explaining automation features" style="left:267px;top:1317px;width:285px;height:160px;background:linear-gradient(135deg,#b9a48f,#6d5a4c)"></div>
  <div class="play" style="left:410px;top:1397px"></div>
  <p class="a" style="left:277px;top:1460px;font-size:6.5px;font-weight:600;color:#fff">BrightLane Automation Features In Action</p>

  <div class="a" style="left:0;top:1512px;width:606px;height:295px;background:var(--dark)"></div>
  <svg class="a" style="left:0;top:1512px" width="606" height="295"><polygon points="606,225 606,295 430,295" fill="var(--blue)"/></svg>
  <h2 class="a h-sec" style="left:55px;top:1549px;width:240px;font-size:11.3px;line-height:1.35;color:#fff">Giveaway Unlimited Incentives That Ranged In Retail Value Of $25-$3,000</h2>
  <div class="a" style="left:55px;top:1604px;width:40px;height:1px;background:var(--blue)"></div>
  <ul class="a chk on-dark" style="left:55px;top:1620px;width:110px">
    <li>Hotel Stays</li><li>Roundtrip Airfare</li><li>7 Night Condo Stays</li><li>Luxury Cruise Getaways</li><li>$100-$500 Dining Cash Cards</li><li>$100-$500 Hotel Savings Cards</li>
  </ul>
  <ul class="a chk on-dark" style="left:176px;top:1620px;width:120px">
    <li>$100 Wine Vouchers</li><li>Premium Wireless Earbuds</li><li>Smartwatches</li><li>Mexico Beach Vacations</li><li>Portable Bluetooth Speakers</li><li>and much more!</li>
  </ul>
  <div class="btn" style="left:55px;top:1750px">Sign Up For a 14 Day Risk Free Trial</div>
  <div class="ph" role="img" aria-label="Desktop, tablet and phone screens showing incentive certificate pages" style="left:335px;top:1560px;width:235px;height:195px;border-radius:6px;background:linear-gradient(140deg,#3a4d8c,#2a8fb8 55%,#1b2740)"></div>
</section>

<section class="page" style="left:677px;top:379px;height:1463px">
  <h2 class="a h-sec" style="left:0;top:36px;width:606px;text-align:center;font-size:13.4px">Done-For-You</h2>
  <div class="a" style="left:283px;top:60px;width:40px;height:1px;background:var(--blue)"></div>
  <p class="a" style="left:0;top:76px;width:606px;text-align:center;font-size:8.3px;color:#444">Promotional marketing assets like a boss!</p>
  <div class="ph" role="img" aria-label="Deep purple network-pattern background" style="left:55px;top:110px;width:497px;height:177px;background:linear-gradient(135deg,#3a2096 0%,#2a1d8a 50%,#3150b0 100%)"></div>
  <div class="a" style="left:72px;top:128px;width:215px;font-size:6.2px;line-height:1.6;color:#e2dff6">
    <p>Imagine having full-colored, professionally designed flyers and posters for each incentive at your disposal...</p>
    <p style="font-weight:600;color:#fff;margin:6px 0">Yes, that's right. We're proud to say we got you covered.</p>
    <p>With a few clicks in your BrightLane dashboard, simply send them in their way to your local print shop or print them from yourself and distribute them as you please...</p>
    <p style="margin-top:6px">Wait, you're telling us you want to stand out and capture the attention of your current customer-base so they keep coming back for more... while nudging those leads that haven't pulled the trigger to finally do business with you?</p>
  </div>
  <div class="a" style="left:320px;top:128px;width:215px;font-size:6.2px;line-height:1.6;color:#e2dff6">
    <p style="font-weight:600;color:#fff;margin-bottom:6px">If you said 'Yes', Woderful...</p>
    <p>Because - from customer appreciation and warm lead letter templates to impactful professionally created promo videos for every incentive proven to maximize just about any marketing campaign... that and so much more will be readily available to you in your BrightLane dashboard!</p>
    <p style="margin-top:6px">Combining your experience (with a tip here and there along the way), consider yourself an unstoppable marketing assassin equipped with high-valued incentives to optimize your marketing efforts - and keep your business pumping like a freak train through whatever economic cycle.</p>
  </div>
  <div class="a" style="left:55px;top:290px;width:397px;height:57px;background:var(--grey)"></div>
  <div class="a" style="left:69px;top:310px;width:14px;height:16px;border:1.2px solid var(--blue);border-radius:2px"></div>
  <p class="a" style="left:100px;top:303px;font-size:6.6px;font-weight:600">Eye-Catching Posters, Flyers &amp; Brochures</p>
  <p class="a txt" style="left:100px;top:315px;width:335px">Professionally made to help you promote the incentives to your audience and designed to maximize offline marketing efforts - at all social events and with every direct mail piece.</p>
  <div class="a" style="left:456px;top:290px;width:46px;height:57px;background:var(--grey)"></div>
  <div class="a" style="left:506px;top:290px;width:46px;height:57px;background:var(--grey)"></div>
  <div class="a" style="left:471px;top:311px;width:16px;height:14px;border:1.2px solid var(--blue);border-radius:2px"></div>
  <div class="a" style="left:521px;top:311px;width:16px;height:14px;border:1.2px solid var(--blue);border-radius:2px"></div>
  <div class="btn c" style="left:303px;top:370px">Sign Up For a 14 Day Risk Free Trial</div>

  <div class="a" style="left:0;top:425px;width:606px;height:387px;background:var(--grey)"></div>
  <p class="a" style="left:231px;top:462px;font-size:8px;font-weight:500;color:var(--blue);border-bottom:1.2px solid var(--blue);padding-bottom:8px">Our Alliances</p>
  <p class="a" style="left:318px;top:462px;font-size:8px;font-weight:500;color:#444">Our Clients</p>
  <div class="logo-box" style="left:55px;top:505px">Grand Solace</div>
  <div class="logo-box" style="left:223px;top:505px">The Tidewater</div>
  <div class="logo-box" style="left:391px;top:505px">Coral Palace</div>
  <div class="logo-box" style="left:55px;top:584px">Voyanza</div>
  <div class="logo-box" style="left:223px;top:584px">Miravista</div>
  <div class="logo-box" style="left:391px;top:584px">StayLink</div>
  <div class="logo-box" style="left:55px;top:662px">Travelia</div>
  <div class="logo-box" style="left:223px;top:662px">Sunhaven</div>
  <div class="logo-box" style="left:391px;top:662px">Open Road Rentals</div>
  <div class="btn c" style="left:303px;top:755px">Sign Up For a 14 Day Risk Free Trial</div>

  <div class="a" style="left:0;top:812px;width:606px;height:341px;background:var(--dark)"></div>
  <h2 class="a h-sec" style="left:0;top:848px;width:606px;text-align:center;font-size:13.4px;color:#fff">Words From Our Customers</h2>
  <div class="ph" role="img" aria-label="Video still of a customer speaking in a recording studio" style="left:160px;top:897px;width:285px;height:161px;background:linear-gradient(135deg,#1f4fa0,#6b5a48 60%,#2a2a30)"></div>
  <div class="play" style="left:303px;top:977px"></div>
  <p class="a" style="left:212px;top:1031px;width:190px;font-size:9px;line-height:1.3;color:#fff;text-align:center;background:rgba(0,0,0,.45)">Hello, I'm Brother Leon Carter from Westbrook, Ca. I've been a veteran</p>
  <div class="a" style="left:55px;top:978px;width:16px;height:16px;border:1px solid var(--blue);border-radius:50%"></div>
  <p class="a" style="left:80px;top:982px;font-size:6.5px;color:var(--blue-lt)">Marcus Dell</p>
  <div class="a" style="left:536px;top:978px;width:16px;height:16px;border:1px solid var(--blue);border-radius:50%"></div>
  <p class="a" style="left:460px;top:976px;width:68px;text-align:right;font-size:6.5px;line-height:1.5;color:var(--blue-lt)">Rina Ostrow<br>Hale</p>
  <div class="btn c" style="left:303px;top:1097px">Sign Up For a 14 Day Risk Free Trial</div>

  <h2 class="a h-sec" style="left:55px;top:1190px;font-size:11.3px">Sounds Too Good To Be True?</h2>
  <div class="bul" style="top:1225px">
    <p>It's very important for you to understand how we are able to do this. First off, hotels and resorts are rarely full but they are always open and still have their fixed costs and always have unused rooms available.</p>
    <p>So what they do is partner up with marketing companies like us to help them fill up their otherwise empty rooms that they end up turning into additional revenue from other parts of their property like their in-house restaurants, the bar, the casino, room service, the spa or even an extra day stay.</p>
    <p>They're actually doing it for some of the same reasons why you would be using our certificates, to increase their repeat and referral business.</p>
    <p>They know that if they show your customers a good time while they're there, they'll be more likely to tell their friends and family about the great time they had and will be more likely to book with the property in the future as a regular paying customer.</p>
  </div>
  <div class="btn" style="left:55px;top:1407px">Sign Up For a 14 Day Risk Free Trial</div>
  <div class="a" style="left:375px;top:1180px;width:194px;height:194px;border-radius:50%;background:#eaf2fb"></div>
  <div class="ph" role="img" aria-label="Video still of a presenter in a suit explaining how the program works" style="left:390px;top:1195px;width:164px;height:164px;border-radius:50%;background:linear-gradient(160deg,#8cc6ea,#2a3a58 70%)"></div>
  <div class="play" style="left:472px;top:1277px"></div>
  <div class="a" style="left:432px;top:1378px;width:12px;height:14px;border:1.2px solid var(--blue)"></div>
  <p class="a" style="left:449px;top:1382px;font-size:6px;color:var(--blue)">— BL —</p>
  <div class="a" style="left:490px;top:1378px;width:12px;height:14px;border:1.2px solid var(--green)"></div>
  <p class="a" style="left:380px;top:1405px;width:184px;text-align:center;font-size:6.3px;color:var(--muted)">Watch Video On 'How Can We Do It?'</p>
</section>

<section class="page" style="left:1318px;top:694px;height:1148px">
  <div class="a" style="left:0;top:0;width:606px;height:383px;background:var(--grey)"></div>
  <div class="ph" role="img" aria-label="100% money back guarantee seal with ribbon" style="left:55px;top:36px;width:126px;height:190px;border-radius:8px;background:linear-gradient(180deg,#3a2da0,#241a78)"></div>
  <h2 class="a h-sec" style="left:216px;top:36px;font-size:13.4px">Risk Free Tial</h2>
  <p class="a" style="left:216px;top:76px;font-size:8.3px;color:#555">14 Days Money Back Guarantee</p>
  <p class="a txt" style="left:216px;top:98px;width:340px">With access to over 30 different incentives in 6 different categories that you get to test offers with it is impossible to effectively test the BrightLane platform in under 14 days.</p>
  <p class="a txt" style="left:216px;top:126px;width:340px">But we are willing to put our money where our mouth is. If you contact us and let us know that you simply made a mistake signing up for our service and we meet all three requirements below we might just refund you in full.</p>
  <div class="a" style="left:231px;top:185px;width:1px;height:85px;border-left:1px dashed var(--blue)"></div>
  <div class="step" style="top:170px"><i></i><span><b>Login</b> to your account and hit the cancel button (pretty basic stuff guys)</span></div>
  <div class="step" style="top:212px"><i></i><span>Request a refund within 14 days by clicking on the <b>support button</b> on every page<br>of this website (with your lame and boring reasoning)</span></div>
  <div class="step" style="top:254px"><i></i><span>Patiently <b>wait</b> for your refund to be processed (yawn...)</span></div>
  <div class="ph" role="img" aria-label="Handwritten owner signature" style="left:216px;top:300px;width:75px;height:45px;background:linear-gradient(90deg,rgba(40,40,60,.08),rgba(40,40,60,.02))"></div>
  <div class="btn" style="left:397px;top:310px">Sign Up For a 14 Day Risk Free Trial</div>

  <div class="a" style="left:0;top:383px;width:606px;height:363px;background:var(--dark)"></div>
  <h2 class="a h-sec" style="left:55px;top:418px;font-size:11.3px;color:#fff">Choose Your Plan</h2>
  <p class="a" style="left:55px;top:437px;font-size:6.4px;color:#c8c9d2">(Each plan has a $199 set up fee)</p>
  <p class="a" style="left:462px;top:427px;font-size:8px;color:var(--blue-lt);border-bottom:1px solid var(--blue-lt);padding-bottom:3px">Monthly</p>
  <p class="a" style="left:520px;top:427px;font-size:8px;color:#fff">Annual</p>
  <div class="ph" role="img" aria-label="Office desk photo with blue overlay" style="left:55px;top:468px;width:133px;height:178px;background:linear-gradient(180deg,#4a4a58,#6b7a94 60%,#8a97ad)"></div>
  <div class="a" style="left:55px;top:482px;width:133px;text-align:center;color:#fff">
    <div class="h-sec" style="font-size:11.3px;line-height:1.3">Unlimited<br>Monthly</div>
    <div style="font-size:22px;font-weight:600;margin-top:22px">$99</div>
    <div style="font-size:8px;color:#e2e4ea">/ month</div>
    <div style="font-size:6.3px;margin-top:36px;line-height:1.5"><b>$298 today</b> then only <b>$99<br>per month</b> thereafter</div>
  </div>
  <ul class="a chk on-dark" style="left:209px;top:469px;width:165px">
    <li>One account can be used for unlimited brands (great for agencies)</li>
    <li>Unlimited access to all our incentives in 6 categories</li>
    <li>Send unlimited incentives from your own business email</li>
    <li>Send unlimited incentives by SMS / text messages</li>
    <li>Automate sending unlimited incentives via landing pages</li>
    <li>Automate sending unlimited incentives via website sticky bars</li>
  </ul>
  <ul class="a chk on-dark" style="left:394px;top:469px;width:160px">
    <li>Automate sending unlimited incentives via website popups</li>
    <li>Automate sending unlimited incentives via our API</li>
    <li>Automate sending unlimited incentives via QR codes</li>
    <li>Automate sending unlimited incentives via our Linkflow App integration</li>
    <li>Eye-catching promo videos, posters and flyers to help you promote the incentives to your audience</li>
    <li>50% commission affiliate program (white label included)</li>
  </ul>
  <div class="btn c" style="left:303px;top:679px">Sign Up For a 14 Day Risk Free Trial</div>

  <div class="a brand" style="left:55px;top:772px"><i></i>BRIGHTLANE PROMO WORKS</div>
  <span class="soc" style="left:467px"></span><span class="soc" style="left:492px"></span><span class="soc" style="left:517px"></span><span class="soc" style="left:542px"></span>
  <div class="a fcol" style="left:55px;top:812px;width:177px">
    <h4>CONTACT US</h4>
    <p><span class="t">BrightLane Promo Group, Inc.</span><br>2740 Harbor View Rd #310<br>Seacliff, CA 90000</p>
    <p><span class="t">Book a Demo</span><br>• New Sales<br>• Current/Past Clients</p>
    <p><span class="t">Call or Text Us</span><br>• New Sales : 1-555-014-2276<br>• Current/Past Clients : 1-555-018-3340</p>
    <p><span class="t">Email Us</span><br>support@brightlanepromoworks.biz</p>
    <p><span class="t">Online Support</span><br>• Monday - Friday 8am : 5pm PST<br>• Sat/Sun/Holidays : <span style="color:#e04a3a">Closed</span><br>• After hours all inquiries will be replied to on the next business day</p>
  </div>
  <div class="a fcol" style="left:267px;top:812px;width:125px">
    <h4>QUICK LINKS</h4>
    <p>Home</p><p>The Incentives</p><p>Login</p><p>Sign Up</p><p>Affiliate</p><p>Integrations</p><p>Testimonials</p><p>Frequently Asked Questions</p><p>BrightLane Distribute Certificate Demo Videos</p><p>White Label Agency Program</p>
  </div>
  <div class="a fcol" style="left:427px;top:812px;width:125px">
    <h4>OTHER LINKS</h4>
    <p>Hoteliers</p><p>BrightLane Certificates List</p><p>How To Use BrightLane Certificates</p><p>Pop Ups &amp; Sticky Bars</p><p>Whitepaper - Increase Sales</p><p>Whitepaper - Improve Sales During Strange Times</p><p>Whitepaper - Boost Website Conversions</p>
  </div>
  <div class="btn c" style="left:303px;top:1074px">Sign Up For a 14 Day Risk Free Trial</div>

  <div class="a" style="left:0;top:1117px;width:606px;height:31px;background:#4a4a52"></div>
  <p class="a" style="left:55px;top:1128px;font-size:6.3px;color:#e0e0e6">© 2024 BrightLane Promo Group, Inc. All Rights Reserved.</p>
  <p class="a" style="left:412px;top:1128px;font-size:6.3px;color:#e0e0e6">Privacy Policy</p>
  <p class="a" style="left:482px;top:1128px;font-size:6.3px;color:#e0e0e6">Terms &amp; Conditions</p>
  <div class="a" style="left:551px;top:1124px;width:55px;height:18px;border-radius:9px 0 0 9px;background:#fff;font-size:6.3px;font-weight:600;color:var(--blue);line-height:18px;padding-left:9px">◉ Support</div>
</section>

</div>
</body>
</html>
```